Designing a website that functions as the shop window for the various aspects of my business -...

I need a website, with separate webpages covering the different components of my practice (small animal consultancy, equine behaviour consultancy, legal case work and education provider). I have a website (www.petcalmstudio.ie) but I haven't updated it in recent years to reflect the newer developments / aspects of my business. Most of my work has been in Ireland but I would like to begin to create an international profile, particularly with regard to the legal casework and offering education within the international horse industry. My overall goal is to improve understanding of animals and animal behaviour, and by doing so, help to reduce the performance of behaviour problems, and also improve animal welfare as a result.

Target Market(s)

Horse and dog owners, horse riders, veterinary surgeons, solicitors

Industry/Entity Type

Legal

Logo Text

Text to be decided on

Number of Pages Required

5+ page

Font styles to use
Sans Serif
Decorative
Script

Colors

Designer to choose colors to be used in the design.

Requirements
Must have
• Relevant content from the attached Flyer including photos
• Use of the phrases:
• 'Understanding Animals'
• Improving animals lives through better understanding
• Science-based, up-to-date relevant information regarding animal behaviour
Nice to have
• 'Leading professional service educating people in understanding animals'
• Separate pages for 1) About, 2) Canine and Feline behaviour Consultancy 3) Equine Consultancy 4) Legal expert witness Consultancy 5) Education 6, FAQs
Should not have
• Prices of services (as these may change from time to time)

```html
<!DOCTYPE html>
<html lang="en">
<head>
<meta charset="utf-8">
<title>Pet Calm Studio</title>
<link href="https://fonts.googleapis.com/css2?family=Lato:wght@400;700;900&display=swap" rel="stylesheet">
<style>
:root{
  --green:#18874d;
  --green-dark:#137a44;
  --ink:#333333;
  --nav:#232323;
  --grey-bg:#f2f2f2;
  --white:#ffffff;
  --orange:#f29a1d;
  --muted:#555555;
}
*{box-sizing:border-box;margin:0;padding:0}
html,body{width:1200px;height:2586px;overflow:hidden;background:var(--white)}
body{font-family:'Lato',Arial,sans-serif;color:var(--ink);position:relative}
.abs{position:absolute}
svg{display:block}

/* header */
.site-header{position:absolute;left:0;top:0;width:1200px;height:103px;background:var(--white)}
.brand{position:absolute;left:76px;top:28px;display:flex;align-items:center;gap:14px}
.brand-dot{width:40px;height:40px;border-radius:50%;background:var(--green)}
.brand-name{font-size:34px;font-weight:700;color:var(--green);letter-spacing:.3px}
.header-contact{position:absolute;left:819px;top:24px;font-size:19px;color:#222}
.header-contact li{list-style:none;display:flex;align-items:center;gap:18px;height:32px}
.header-contact svg{width:16px;height:16px;fill:var(--green)}

/* nav */
.main-nav{position:absolute;left:0;top:103px;width:1200px;height:55px;background:var(--nav)}
.main-nav ul{list-style:none;display:flex;justify-content:space-between;align-items:center;height:55px;margin:0 74px 0 76px}
.main-nav a{color:var(--white);text-decoration:none;font-size:12.5px;font-weight:700;text-transform:uppercase;letter-spacing:.2px}

/* hero */
.hero{position:absolute;left:0;top:158px;width:1200px;height:506px}
.hero-panel{position:absolute;left:0;top:0;width:526px;height:506px;background:var(--green)}
.hero-title{position:absolute;left:76px;top:112px;font-size:40px;line-height:44px;font-weight:900;color:var(--white)}
.hero-points{position:absolute;left:76px;top:208px;width:430px;list-style:none;color:var(--white);font-size:18px;line-height:25px}
.hero-points li{position:relative;padding-left:34px;margin-bottom:12px}
.hero-points svg{position:absolute;left:0;top:4px;width:17px;height:17px}
.hero-dots{position:absolute;left:76px;top:444px;display:flex;gap:11px}
.hero-dots span{width:12px;height:12px;border-radius:50%;background:#1f1f1f}
.hero-dots span.active{background:var(--white)}
.hero-photo{position:absolute;left:526px;top:0;width:674px;height:506px;background:linear-gradient(135deg,#2b2b2b 0%,#5e554b 35%,#8c7f70 60%,#b7b2aa 100%)}

/* welcome */
.welcome{position:absolute;left:0;top:664px;width:1200px;height:444px}
.welcome-title{position:absolute;left:76px;top:56px;font-size:29px;line-height:29px;font-weight:900;color:#222;text-transform:uppercase}
.welcome-title span{display:block;color:var(--green)}
.welcome-text{position:absolute;left:76px;top:128px;width:600px;font-size:14.5px;line-height:27px;color:var(--ink)}
.btn{display:inline-flex;align-items:center;justify-content:center;background:var(--green);color:var(--white);font-size:14.5px;font-weight:700;text-transform:uppercase;text-decoration:none}
.welcome .btn{position:absolute;left:76px;top:341px;width:150px;height:46px}
.welcome-photo{position:absolute;left:703px;top:60px;width:423px;height:328px;background:linear-gradient(160deg,#2a2f3a 0%,#3c4d6c 40%,#2a2a26 75%,#6b5a22 100%)}

/* offer */
.offer{position:absolute;left:0;top:1108px;width:1200px;height:595px;background:var(--grey-bg)}
.section-title{position:absolute;left:0;width:1200px;text-align:center;font-size:27px;font-weight:700;color:#333;text-transform:uppercase}
.offer .section-title{top:48px}
.slider-arrow{position:absolute;width:20px;height:30px}
.slider-arrow path{fill:none;stroke:#777;stroke-width:3.5}
.offer-card{position:absolute;top:109px;width:330px;height:412px;background:var(--white);text-align:center}
.offer-photo{width:330px;height:197px}
.offer-card h3{margin-top:30px;font-size:19px;font-weight:900;color:var(--green);text-transform:uppercase}
.offer-card p{margin:10px 22px 0;font-size:14.5px;line-height:27px;color:var(--ink)}
.offer-card .btn{position:absolute;left:95px;top:388px;width:150px;height:47px}

/* components */
.components{position:absolute;left:0;top:1703px;width:1200px;height:487px}
.components .section-title{top:52px}
.component{position:absolute;top:138px;width:300px;text-align:center}
.component-icon{width:114px;height:114px;margin:0 auto;border:2.5px solid #222;border-radius:50%;display:flex;align-items:center;justify-content:center}
.component-icon svg{width:48px;height:48px;fill:#222}
.component h3{margin-top:32px;font-size:19px;line-height:26px;font-weight:900;color:var(--green);text-transform:uppercase}

/* footer band */
.signup-band{position:absolute;left:0;top:2190px;width:1200px;height:79px;background:var(--green-dark)}
.footer-badge{position:absolute;left:78px;top:-52px;width:117px;height:117px;border-radius:50%;background:var(--white)}
.signup-label,.follow-label{position:absolute;top:28px;font-size:17px;font-weight:700;color:var(--white);text-transform:uppercase}
.signup-label{left:362px}
.follow-label{left:814px}
.signup-input{position:absolute;left:502px;top:22px;width:236px;height:35px;background:var(--white);font-size:13px;color:#333;padding:9px 12px}
.signup-go{position:absolute;left:738px;top:22px;width:38px;height:35px;background:var(--orange);display:flex;align-items:center;justify-content:center}
.social{position:absolute;left:930px;top:26px;display:flex;gap:22px}
.social span{width:26px;height:26px;border-radius:50%;background:var(--white)}

/* footer */
.site-footer{position:absolute;left:0;top:2269px;width:1200px;height:317px;background:var(--green)}
.footer-col{position:absolute;top:42px;color:var(--white)}
.footer-col h4{font-size:17px;font-weight:700;text-transform:uppercase;margin-bottom:12px}
.footer-col li{list-style:none;font-size:14px;line-height:29.5px}
.footer-col .icon-row{display:flex;align-items:center;gap:18px;font-size:14px}
.footer-col .icon-row svg{width:14px;height:14px;fill:var(--white)}
.footer-brand{display:flex;align-items:center;gap:10px;margin-top:26px}
.footer-brand .brand-dot{width:26px;height:26px;background:var(--white)}
.footer-brand .brand-name{font-size:21px;color:var(--white)}
.copyright{margin-top:12px;font-size:12.5px;line-height:21px}
</style>
</head>
<body>

<header class="site-header">
  <div class="brand"><span class="brand-dot"></span><span class="brand-name">Pet Calm Studio</span></div>
  <ul class="header-contact">
    <li><svg viewBox="0 0 24 24"><path d="M6.6 10.8a15.1 15.1 0 0 0 6.6 6.6l2.2-2.2a1 1 0 0 1 1-.25 11.4 11.4 0 0 0 3.6.57 1 1 0 0 1 1 1V20a1 1 0 0 1-1 1A17 17 0 0 1 3 4a1 1 0 0 1 1-1h3.5a1 1 0 0 1 1 1c0 1.25.2 2.45.57 3.57a1 1 0 0 1-.25 1z"/></svg>87 555 0194</li>
    <li><svg viewBox="0 0 24 24"><path d="M2 5h20v2l-10 6L2 7zm0 4 10 6 10-6v10H2z"/></svg>hello@petcalmstudio.ie</li>
  </ul>
</header>

<nav class="main-nav">
  <ul>
    <li><a href="#">Home</a></li>
    <li><a href="#">About</a></li>
    <li><a href="#">Canine and Feline Behaviour Consultancy</a></li>
    <li><a href="#">Equine Consultancy</a></li>
    <li><a href="#">Legal Expert Witness Consultancy</a></li>
    <li><a href="#">Education</a></li>
    <li><a href="#">Contact Us</a></li>
  </ul>
</nav>

<section class="hero">
  <div class="hero-panel">
    <h1 class="hero-title">PET CALM<br>STUDIO</h1>
    <ul class="hero-points">
      <li><svg viewBox="0 0 20 20"><circle cx="10" cy="10" r="10" fill="#fff"/><path d="M5.5 10.2l3 3 6-6" fill="none" stroke="#18874d" stroke-width="2.6"/></svg>Understanding Animals.</li>
      <li><svg viewBox="0 0 20 20"><circle cx="10" cy="10" r="10" fill="#fff"/><path d="M5.5 10.2l3 3 6-6" fill="none" stroke="#18874d" stroke-width="2.6"/></svg>Improving animals lives through better understanding.</li>
      <li><svg viewBox="0 0 20 20"><circle cx="10" cy="10" r="10" fill="#fff"/><path d="M5.5 10.2l3 3 6-6" fill="none" stroke="#18874d" stroke-width="2.6"/></svg>Science-based, up-to-date relevant information regarding animal behaviour.</li>
    </ul>
    <div class="hero-dots"><span class="active"></span><span></span><span></span><span></span></div>
  </div>
  <div class="hero-photo" role="img" aria-label="Close-up photo of a small grey terrier dog looking up"></div>
</section>

<section class="welcome">
  <h2 class="welcome-title">Welcome to<span>Pet Calm Studio</span></h2>
  <p class="welcome-text">Animals have been used by humans for a variety of purposes, including as a source of food, for hunting, for mobility, to help win battles, for sport - and most recently, for companionship. Whether we are dog or cat lovers, horseriders or owners, through the course of our relationship with our animals, many of us will be faced with problem behaviours, such as aggression, excessive barking, destructiveness (dogs), spraying, fear problems, aggression (cats), bucking, refusing to load into trailers, rearing, shying (horses).</p>
  <a class="btn" href="#">Read More</a>
  <div class="welcome-photo" role="img" aria-label="Photo of a lecture with an audience watching a projected slide"></div>
</section>

<section class="offer">
  <h2 class="section-title">What We Offer</h2>
  <svg class="slider-arrow" style="left:44px;top:308px" viewBox="0 0 20 30"><path d="M16 3 4 15l12 12"/></svg>
  <svg class="slider-arrow" style="left:1136px;top:308px" viewBox="0 0 20 30"><path d="M4 3l12 12L4 27"/></svg>

  <article class="offer-card" style="left:76px">
    <div class="offer-photo" role="img" aria-label="Photo of a dark dog beside torn paper on a tiled floor" style="background:linear-gradient(135deg,#6d6a63,#2b2a28 55%,#8a867e)"></div>
    <h3>Behaviour Consultations</h3>
    <p>During a behaviour consultation, an individual assessment of the horse is carried out, incorporating information regarding the horses health..</p>
    <a class="btn" href="#">Read More</a>
  </article>

  <article class="offer-card" style="left:435px">
    <div class="offer-photo" role="img" aria-label="Photo of a trainer outdoors with a collie dog" style="background:linear-gradient(135deg,#3f5a2a,#8aa35a 50%,#c9c28e)"></div>
    <h3>Training Sessions</h3>
    <p>Individual training sessions with horse and rider, designed to address training problems, the performance of problem behaviours or general poor performance.</p>
    <a class="btn" href="#">Read More</a>
  </article>

  <article class="offer-card" style="left:795px">
    <div class="offer-photo" role="img" aria-label="Photo of a horse and rider splashing through a cross-country water jump" style="background:linear-gradient(180deg,#8c8a5e,#9a8a66 50%,#c7c7c0)"></div>
    <h3>Training Your Horse</h3>
    <p>This course incorporates both classroom sessions and practical sessions in the arena, developing the rider skills in training both in hand and under saddle..</p>
    <a class="btn" href="#">Read More</a>
  </article>
</section>

<section class="components">
  <h2 class="section-title">Components</h2>
  <svg class="slider-arrow" style="left:44px;top:250px" viewBox="0 0 20 30"><path d="M16 3 4 15l12 12"/></svg>
  <svg class="slider-arrow" style="left:1136px;top:250px" viewBox="0 0 20 30"><path d="M4 3l12 12L4 27"/></svg>

  <div class="component" style="left:90px">
    <div class="component-icon"><svg viewBox="0 0 24 24"><circle cx="12" cy="7" r="4"/><path d="M4 21c0-4.4 3.6-7 8-7s8 2.6 8 7z"/></svg></div>
    <h3>Small<br>Animal Consultancy</h3>
  </div>
  <div class="component" style="left:450px">
    <div class="component-icon"><svg viewBox="0 0 24 24"><path d="M9 4c4.4 0 8 2.7 8 6s-3.6 6-8 6c-.9 0-1.7-.1-2.5-.3L3 17.5l1.2-3.1C2.8 13.3 1 11.8 1 10c0-3.3 3.6-6 8-6z"/><path d="M18.5 9.5c2.7.8 4.5 2.8 4.5 5 0 1.5-.8 2.8-2 3.7l1 2.8-3.3-1.6c-.7.2-1.4.3-2.2.3-2 0-3.8-.6-5-1.6 4 0 7.1-2.5 7-8.6z"/></svg></div>
    <h3>Equine Behaviour<br>Consultancy</h3>
  </div>
  <div class="component" style="left:810px">
    <div class="component-icon"><svg viewBox="0 0 24 24"><path d="M5 2h9l5 5v15H5z"/><path d="M8 11h8M8 14h8M8 17h8" stroke="#fff" stroke-width="1.6"/><path d="M14 2v5h5" fill="#fff"/></svg></div>
    <h3 style="margin-top:38px">Legal<br>Case Work</h3>
  </div>
</section>

<section class="signup-band">
  <div class="footer-badge"></div>
  <span class="signup-label">Email Sign Up</span>
  <div class="signup-input">Enter Email Address</div>
  <div class="signup-go"><svg width="12" height="14" viewBox="0 0 12 14"><path d="M3 2l5 5-5 5" fill="none" stroke="#fff" stroke-width="2.6"/></svg></div>
  <span class="follow-label">Follow Us</span>
  <div class="social"><span></span><span></span><span></span><span></span><span></span></div>
</section>

<footer class="site-footer">
  <div class="footer-col" style="left:76px">
    <h4>Site Map</h4>
    <ul><li>Home</li><li>About</li><li>Canine and Feline behaviour Consultancy</li><li>Equine Consultancy</li><li>Legal expert witness Consultancy</li><li>Education</li><li>Contact us</li></ul>
  </div>
  <div class="footer-col" style="left:379px">
    <h4>What We Offer</h4>
    <ul><li>Behaviour consultations</li><li>Training sessions</li><li>Training your horse</li><li>Training, performance and welfare</li></ul>
  </div>
  <div class="footer-col" style="left:648px">
    <h4>Education</h4>
    <ul><li>Donec id consequat</li><li>Nunc facilisis scelerisque</li><li>mauris commodo</li><li>Rhoncus</li></ul>
  </div>
  <div class="footer-col" style="left:864px">
    <h4>Contact Us</h4>
    <ul>
      <li class="icon-row"><svg viewBox="0 0 24 24"><path d="M6.6 10.8a15.1 15.1 0 0 0 6.6 6.6l2.2-2.2a1 1 0 0 1 1-.25 11.4 11.4 0 0 0 3.6.57 1 1 0 0 1 1 1V20a1 1 0 0 1-1 1A17 17 0 0 1 3 4a1 1 0 0 1 1-1h3.5a1 1 0 0 1 1 1c0 1.25.2 2.45.57 3.57a1 1 0 0 1-.25 1z"/></svg>87 555 0194</li>
      <li class="icon-row"><svg viewBox="0 0 24 24"><path d="M2 5h20v2l-10 6L2 7zm0 4 10 6 10-6v10H2z"/></svg>hello@petcalmstudio.ie</li>
    </ul>
    <div class="footer-brand"><span class="brand-dot"></span><span class="brand-name">Pet Calm Studio</span></div>
    <p class="copyright">Copyright © 2019. Company Name.<br>All Right Reserved</p>
  </div>
</footer>

</body>
</html>
```